BMR Going Cashless

Hello,
We are a medical office looking to get a flyer created to promote to our patients we will be going "Cashless." Our tagline will be "Cash-Less is Stress-Less"

"Starting in July, to offer you the fastest and most convenient service, we are transitioning to a cashless system. You can now enjoy faster checkout times and greater security with card and contactless payments. More info to come."

I've added two other flyers as sample designs we've used.

Please include logo, addresses, website, phone number

Files to include jpeg, png, pdf (under 5mb), Facebook and Instagram sizing.

Thank you,
Lowen

```html
<!DOCTYPE html>
<html lang="en">
<head>
<meta charset="utf-8">
<title>BMR Going Cashless</title>
<link href="https://fonts.googleapis.com/css2?family=Jost:wght@400;500;600;700&family=Kaushan+Script&display=swap" rel="stylesheet">
<style>
  :root {
    --backdrop: #5d5e60;
    --ink: #000000;
    --slate: #6d6e71;
    --orange: #f47b45;
    --orange-line: #f58220;
    --teal: #2bbfa4;
    --white: #ffffff;
  }
  * { margin: 0; padding: 0; box-sizing: border-box; }
  html, body {
    width: 1200px; height: 1144px; overflow: hidden;
    background: var(--backdrop);
    font-family: "Jost", sans-serif;
  }
  .flyer {
    position: absolute; left: 134px; top: 106px;
    width: 931px; height: 931px;
    background: var(--slate); overflow: hidden;
    box-shadow: 0 10px 40px rgba(0,0,0,.35);
  }
  .flyer > * { position: absolute; }
  .shapes { left: 0; top: 0; width: 931px; height: 931px; }
  .brand {
    left: 0; width: 931px; top: 58px;
    display: flex; justify-content: center; align-items: center; gap: 14px;
  }
  .brand-dot { width: 34px; height: 34px; border-radius: 50%; background: var(--teal); }
  .brand-name {
    color: var(--orange); font-weight: 700; font-size: 34px;
    line-height: 1; letter-spacing: .5px;
  }
  .script {
    left: 0; width: 931px; text-align: center;
    font-family: "Kaushan Script", cursive;
    color: var(--orange);
    -webkit-text-stroke: 8px var(--white);
    paint-order: stroke fill;
    text-shadow: 3px 5px 6px rgba(0,0,0,.35);
  }
  .headline { top: 140px; font-size: 128px; line-height: 1.2; }
  .start-date { top: 410px; font-size: 98px; line-height: 1.2; }
  .tagline-band {
    left: 0; top: 325px; width: 931px; height: 80px;
    background: var(--white);
    display: flex; align-items: center; justify-content: center;
  }
  .tagline {
    color: var(--teal); font-weight: 600; font-size: 54px;
    letter-spacing: 3px; line-height: 1;
  }
  .message {
    left: 61px; top: 550px; width: 808px;
    color: var(--white); font-size: 25px; line-height: 40px;
    text-align: justify; text-align-last: center; letter-spacing: .6px;
  }
  .more-info {
    right: 44px; top: 712px;
    color: var(--white); font-weight: 500; font-size: 34px; letter-spacing: 2px; line-height: 1;
  }
  .location {
    top: 776px; color: var(--white); font-size: 15.5px; line-height: 26px; letter-spacing: .4px;
  }
  .location-one { left: 117px; text-align: left; }
  .location-two { left: 400px; width: 190px; text-align: center; }
  .location-three { right: 66px; text-align: right; }
  .pin { width: 40px; height: 40px; }
  .pin-one { left: 66px; top: 775px; }
  .pin-two { left: 359px; top: 775px; }
  .pin-three { left: 644px; top: 775px; }
  .divider { top: 780px; width: 2px; height: 62px; background: var(--white); }
  .divider-one { left: 320px; }
  .divider-two { left: 610px; }
  .contact-icon { width: 40px; height: 40px; top: 870px; }
  .phone-icon { left: 65px; }
  .web-icon { left: 441px; }
  .contact-text {
    top: 866px; color: var(--orange); font-weight: 700; font-size: 33px;
    letter-spacing: 3.5px; line-height: 48px;
  }
  .phone-number { left: 114px; }
  .web-address { left: 492px; letter-spacing: 3.2px; }
</style>
</head>
<body>
  <main class="flyer">
    <svg class="shapes" viewBox="0 0 931 931" aria-hidden="true">
      <path d="M0 0 H931 V267 L900 264 L870 270 L835 262 L800 268 L760 263 L720 269 L690 262 L650 266 L610 261 L560 268 L520 260 L470 266 L430 259 L390 268 L350 262 L310 270 L270 263 L230 257 L200 265 L160 258 L120 266 L80 259 L40 264 L0 262 Z" fill="var(--ink)"/>
      <path d="M0 749 H475 C520 749 540 708 585 708 H931 V862 H0 Z" fill="var(--ink)"/>
      <path d="M0 737 H465 C510 737 525 695 575 695 H931" fill="none" stroke="var(--orange-line)" stroke-width="6"/>
      <rect x="0" y="862" width="931" height="69" fill="var(--white)"/>
    </svg>

    <div class="brand">
      <span class="brand-dot"></span>
      <span class="brand-name">BMR FOOT &amp; ANKLE</span>
    </div>

    <h1 class="script headline">Cashless</h1>

    <div class="tagline-band">
      <p class="tagline">Cash–Less is Stress–Less</p>
    </div>

    <h2 class="script start-date">Starting in July</h2>

    <p class="message">to offer you the fastest and most convenient service, we are transitioning to a cashless system. You can now enjoy faster checkout times and greater security with card and contactless payments.</p>

    <p class="more-info">More info to come</p>

    <svg class="pin pin-one" viewBox="0 0 40 40" aria-hidden="true"><circle cx="20" cy="20" r="20" fill="var(--orange)"/><path d="M20 9a8 8 0 0 0-8 8c0 6 8 14 8 14s8-8 8-14a8 8 0 0 0-8-8z" fill="var(--white)"/><circle cx="20" cy="17" r="3.2" fill="var(--orange)"/></svg>
    <svg class="pin pin-two" viewBox="0 0 40 40" aria-hidden="true"><circle cx="20" cy="20" r="20" fill="var(--orange)"/><path d="M20 9a8 8 0 0 0-8 8c0 6 8 14 8 14s8-8 8-14a8 8 0 0 0-8-8z" fill="var(--white)"/><circle cx="20" cy="17" r="3.2" fill="var(--orange)"/></svg>
    <svg class="pin pin-three" viewBox="0 0 40 40" aria-hidden="true"><circle cx="20" cy="20" r="20" fill="var(--orange)"/><path d="M20 9a8 8 0 0 0-8 8c0 6 8 14 8 14s8-8 8-14a8 8 0 0 0-8-8z" fill="var(--white)"/><circle cx="20" cy="17" r="3.2" fill="var(--orange)"/></svg>

    <address class="location location-one">210 Orchard Hill Dr.<br>Suite 140<br>Brookmere, MD 21790</address>
    <span class="divider divider-one"></span>
    <address class="location location-two">58 Meadow Park Lane<br>Elkridge Falls, WV 25490</address>
    <span class="divider divider-two"></span>
    <address class="location location-three">4120 Linden Grove Blvd.<br>Suite 305<br>Ashby, MD 21795</address>

    <svg class="contact-icon phone-icon" viewBox="0 0 40 40" aria-hidden="true"><circle cx="20" cy="20" r="20" fill="var(--teal)"/><rect x="13" y="9" width="14" height="22" rx="3" fill="none" stroke="var(--white)" stroke-width="2.5"/><circle cx="20" cy="27" r="1.3" fill="var(--white)"/></svg>
    <p class="contact-text phone-number">(877)555-0142</p>

    <svg class="contact-icon web-icon" viewBox="0 0 40 40" aria-hidden="true"><circle cx="20" cy="20" r="20" fill="var(--teal)"/><g fill="none" stroke="var(--white)" stroke-width="2"><circle cx="20" cy="20" r="11"/><ellipse cx="20" cy="20" rx="5" ry="11"/><path d="M9 20h22M20 9v22"/></g></svg>
    <p class="contact-text web-address">www.bmrfootcare.com</p>
  </main>
</body>
</html>
```